Card Design for my dog training business Brightpaw Obedience

Need a business card design for my dog training business with my new logo. Want the card to come off professional yet fun. Want it to be very eye catchy as well. I normally have these at vet clinics, pet stores, and groomers. so need it to look better than my competitors.
Target Market(s)
dog owners
Industry/Entity Type
Dog Training
Contact Information for Business Card
needs logo, my name and info
Font styles to use
Serif
Colors
0255a3
ffffff
ec1f27
000000
333333
fbfbfb
Requirements
Must have
- Brightpaw Obedience
- Felix Orland
- 415 903 2276
- info@brightpawobedience.example
- www.brightpawobedience.example

```html
<!DOCTYPE html>
<html lang="en">
<head>
<meta charset="utf-8">
<title>Brightpaw Obedience — Business Card</title>
<link rel="stylesheet" href="https://fonts.googleapis.com/css2?family=Noto+Serif:ital,wght@0,400;1,400&display=swap">
<style>
  :root {
    --brand-blue: #0255a3;
    --brand-blue-deep: #034b8f;
    --brand-red: #ec1f27;
    --paper: #fbfbfb;
    --white: #ffffff;
    --ink: #000000;
    --charcoal: #333333;
    --backdrop: #c4c4c4;
    --serif: "Noto Serif", Georgia, serif;
  }
  * { margin: 0; padding: 0; box-sizing: border-box; }
  html, body {
    width: 1200px; height: 576px; overflow: hidden;
    background: var(--backdrop);
    font-family: var(--serif);
  }
  .canvas { position: relative; width: 1200px; height: 576px; }

  .card {
    position: absolute; width: 484px; height: 294px; top: 138px;
    border-radius: 13px; overflow: hidden;
    box-shadow: 0 3px 8px rgba(0,0,0,.35);
  }

  /* Back of card */
  .card--back { left: 82px; background: var(--brand-blue-deep); }
  .card--back .brand {
    position: absolute; left: 0; right: 0; top: 78px;
    display: flex; flex-direction: column; align-items: center; gap: 12px;
  }
  .brand-dot { width: 54px; height: 54px; border-radius: 50%; }
  .card--back .brand-dot { background: var(--white); }
  .card--back .brand-name { color: var(--white); font-size: 18px; letter-spacing: .5px; }
  .tagline-band {
    position: absolute; left: 0; right: 0; top: 256px; height: 28px;
    background: var(--ink); color: var(--white);
    display: flex; align-items: center; justify-content: center;
    font-style: italic; font-size: 11px;
  }

  /* Front of card */
  .card--front { left: 602px; width: 480px; height: 292px; background: var(--paper); }
  .card-panels { position: absolute; inset: 0; }
  .card--front .brand {
    position: absolute; left: 0; width: 236px; top: 86px;
    display: flex; flex-direction: column; align-items: center; gap: 12px;
  }
  .card--front .brand-dot { background: var(--brand-blue); }
  .card--front .brand-name { color: var(--brand-blue); font-size: 15px; letter-spacing: .3px; }

  .holder {
    position: absolute; right: 24px; top: 42px; text-align: right; color: var(--white);
  }
  .holder-name { font-size: 21px; line-height: 1.2; }
  .holder-role { font-size: 12px; margin-top: 2px; }

  .contact-list {
    position: absolute; right: 24px; top: 209px;
    list-style: none; color: var(--white); font-size: 11.5px;
  }
  .contact-list li {
    display: flex; align-items: center; justify-content: flex-end; gap: 9px;
    height: 19px;
  }
  .contact-icon { width: 12px; height: 12px; fill: var(--white); flex: none; }
</style>
</head>
<body>
<div class="canvas">

  <section class="card card--back" aria-label="Card back">
    <div class="brand">
      <span class="brand-dot" aria-hidden="true"></span>
      <span class="brand-name">Brightpaw Obedience</span>
    </div>
    <p class="tagline-band">“Patient training for happy dogs, one walk at a time.”</p>
  </section>

  <section class="card card--front" aria-label="Card front">
    <svg class="card-panels" width="480" height="292" viewBox="0 0 480 292" aria-hidden="true">
      <path d="M190,0 Q278,146 190,292 L480,292 L480,0 Z" fill="var(--brand-red)"/>
      <path d="M198,0 Q286,146 198,292 L480,292 L480,0 Z" fill="var(--brand-blue-deep)"/>
      <circle cx="484" cy="88" r="14" fill="var(--brand-red)"/>
    </svg>

    <div class="brand">
      <span class="brand-dot" aria-hidden="true"></span>
      <span class="brand-name">Brightpaw Obedience</span>
    </div>

    <div class="holder">
      <p class="holder-name">Felix Orland</p>
      <p class="holder-role">Dog Trainer</p>
    </div>

    <ul class="contact-list">
      <li>415 903 2276
        <svg class="contact-icon" viewBox="0 0 12 12" aria-hidden="true"><path d="M1 4 Q6 0 11 4 L9.5 5.5 L8 4.5 L8 3.5 Q6 3 4 3.5 L4 4.5 L2.5 5.5 Z M3 6 L9 6 L10 11 L2 11 Z"/></svg>
      </li>
      <li>info@brightpawobedience.example
        <svg class="contact-icon" viewBox="0 0 12 12" aria-hidden="true"><path d="M0.5 2.5 H11.5 V9.5 H0.5 Z M1.5 3.5 L6 7 L10.5 3.5 V3.2 H1.5 Z" fill-rule="evenodd"/></svg>
      </li>
      <li>www.brightpawobedience.example
        <svg class="contact-icon" viewBox="0 0 12 12" aria-hidden="true"><circle cx="6" cy="6" r="5" fill="none" stroke="#fff" stroke-width="1"/><ellipse cx="6" cy="6" rx="2.2" ry="5" fill="none" stroke="#fff" stroke-width="0.9"/><path d="M1 6 H11" stroke="#fff" stroke-width="0.9"/></svg>
      </li>
    </ul>
  </section>

</div>
</body>
</html>
```